We are a recruitment company based in Norwich/Cambridge England.
I have included our company logo which we want to remain the same.

What we are looking for is a new creative Business card which will really stand out!!

Contact Information for Business Card

Harriet Dunmore
email: Harriet@plavex.co.uk
Address: Brackwell House
Fenmoor Enterprise Park
Partridge Way
Norwich
QB9 3KX
Tel:01632 960418

```html
<!DOCTYPE html>
<html lang="en">
<head>
<meta charset="utf-8">
<title>Plavex Business Card</title>
<link href="https://fonts.googleapis.com/css2?family=Lato:wght@400;700&display=swap" rel="stylesheet">
<style>
  :root {
    --backdrop: #2b2b2b;
    --paper: #f1f1f1;
    --brand-green: #7fba3a;
    --brand-grey: #8a878b;
    --ink: #4a4a4a;
    --ink-soft: #7a7a7a;
    --rule: #c9c9c9;
    --white: #ffffff;
  }
  * { margin: 0; padding: 0; box-sizing: border-box; }
  html, body {
    width: 1200px; height: 960px; overflow: hidden;
    background: var(--backdrop);
    font-family: "Lato", Arial, sans-serif;
  }
  .canvas { position: relative; width: 1200px; height: 960px; }

  .card {
    position: absolute; width: 600px; height: 343px;
    border-radius: 20px; overflow: hidden;
  }
  .card--front { left: 314px; top: 113px; background: var(--paper); }
  .card--back { left: 311px; top: 472px; background: var(--brand-green); }

  .brand {
    position: absolute; left: 64px; top: 128px;
    display: flex; align-items: center; gap: 12px;
  }
  .brand__dot {
    width: 46px; height: 46px; border-radius: 50%;
    background: var(--brand-green);
  }
  .brand__text { display: flex; flex-direction: column; }
  .brand__name {
    font-size: 40px; font-weight: 700; color: var(--brand-grey);
    line-height: 1; letter-spacing: -0.5px;
  }
  .brand__tagline {
    font-size: 7.5px; font-weight: 700; color: var(--brand-grey);
    letter-spacing: 1.3px; margin-top: 3px; padding-left: 2px;
  }

  .divider {
    position: absolute; left: 337px; top: 80px;
    width: 1px; height: 165px; background: var(--rule);
  }

  .contact { position: absolute; left: 365px; top: 71px; color: var(--ink); }
  .contact__name {
    font-size: 22px; font-weight: 700; color: var(--brand-green);
    line-height: 1.1; text-transform: uppercase;
  }
  .contact__role {
    font-size: 16px; color: var(--ink-soft); text-transform: uppercase;
    line-height: 1.1; margin-top: 1px;
  }
  .contact__address { font-size: 15px; line-height: 19px; margin-top: 17px; }
  .contact__lines { list-style: none; margin-top: 11px; }
  .contact__line {
    display: flex; align-items: center; gap: 8px;
    font-size: 14.5px; line-height: 19px;
  }
  .contact__icon { width: 14px; height: 14px; flex: none; }

  .band {
    position: absolute; left: 0; top: 295px; width: 600px; height: 29px;
    display: flex;
  }
  .band__green {
    flex: 0 0 436px; background: var(--brand-green);
    display: flex; align-items: center; padding-left: 127px;
  }
  .band__grey {
    flex: 1; background: var(--brand-grey);
    display: flex; align-items: center; padding-left: 14px;
  }
  .band__url {
    color: var(--white); font-size: 13px; letter-spacing: 5px;
  }
  .band__dot {
    width: 22px; height: 22px; border-radius: 50%; background: var(--white);
    margin-left: -28px;
  }

  .back-brand {
    position: absolute; left: 0; top: 110px; width: 100%;
    display: flex; justify-content: center; align-items: center; gap: 18px;
  }
  .back-brand__dot {
    width: 64px; height: 64px; border-radius: 50%; background: var(--white);
  }
  .back-brand__name {
    font-size: 64px; font-weight: 700; color: var(--white); line-height: 1;
  }
  .back-url {
    position: absolute; left: 0; top: 299px; width: 100%;
    text-align: center; color: var(--white);
    font-size: 14px; letter-spacing: 5px;
  }
</style>
</head>
<body>
<main class="canvas">

  <section class="card card--front" aria-label="Business card front">
    <div class="brand">
      <span class="brand__dot"></span>
      <div class="brand__text">
        <span class="brand__name">Plavex</span>
        <span class="brand__tagline">Technology Recruitment</span>
      </div>
    </div>

    <div class="divider"></div>

    <div class="contact">
      <h1 class="contact__name">Harriet Dunmore</h1>
      <p class="contact__role">Director</p>
      <p class="contact__address">Brackwell House<br>Partridge Way, QB9 3KX</p>
      <ul class="contact__lines">
        <li class="contact__line">
          <svg class="contact__icon" viewBox="0 0 24 24"><path fill="#7fba3a" d="M6.6 10.8c1.4 2.8 3.8 5.1 6.6 6.6l2.2-2.2c.3-.3.7-.4 1-.2 1.1.4 2.3.6 3.6.6.6 0 1 .4 1 1V20c0 .6-.4 1-1 1C10.6 21 3 13.4 3 4c0-.6.4-1 1-1h3.5c.6 0 1 .4 1 1 0 1.3.2 2.5.6 3.6.1.3 0 .7-.2 1z"/></svg>
          01632 960418
        </li>
        <li class="contact__line">
          <svg class="contact__icon" viewBox="0 0 24 24"><rect x="6" y="1" width="12" height="22" rx="2" fill="#7fba3a"/><rect x="8" y="4" width="8" height="14" fill="#f1f1f1"/></svg>
          07700 900265
        </li>
        <li class="contact__line">
          <svg class="contact__icon" viewBox="0 0 24 24"><rect x="6" y="2" width="12" height="7" fill="#7fba3a"/><rect x="2" y="10" width="20" height="8" rx="1" fill="#7fba3a"/><rect x="6" y="15" width="12" height="7" fill="#7fba3a" stroke="#f1f1f1" stroke-width="1.5"/></svg>
          01632 960733
        </li>
        <li class="contact__line">
          <svg class="contact__icon" viewBox="0 0 24 24"><rect x="2" y="5" width="20" height="14" fill="#7fba3a"/><path d="M2 5l10 8 10-8" fill="none" stroke="#f1f1f1" stroke-width="1.5"/></svg>
          Harriet@plavex.co.uk
        </li>
      </ul>
    </div>

    <div class="band">
      <div class="band__green"><span class="band__url">www.plavex.co.uk</span></div>
      <div class="band__grey"><span class="band__dot"></span></div>
    </div>
  </section>

  <section class="card card--back" aria-label="Business card back">
    <div class="back-brand">
      <span class="back-brand__dot"></span>
      <span class="back-brand__name">Plavex</span>
    </div>
    <p class="back-url">www.plavex.co.uk</p>
  </section>

</main>
</body>
</html>
```